Best local air conditioning and heating contractor

We need a website design for a new company in Tampa Bay called the Coastal Breeze Cooling Company. We provide superior services for residential and commercial properties as well as maintenance and installing HVAC systems. We also want to sell equipment, parts and filter on the website as well. We want it easy to use for customers. Rich with content and keywords for our area.

Target Market(s)

homeowners in Tampa Bay

Industry/Entity Type

HVAC air conditioning and heating

Coding

Coded - Design and coding required

Number of Pages Required

5+ page

Font styles to use
Sans Serif

Requirements
Nice to have
• would like the colors to be same as logo

```html
<!DOCTYPE html>
<html lang="en">
<head>
<meta charset="utf-8">
<title>Coastal Breeze Cooling Company</title>
<link href="https://fonts.googleapis.com/css2?family=Michroma&family=Oswald:wght@400;500;600&family=Montserrat:wght@400;500;600&display=swap" rel="stylesheet">
<style>
:root{
  --red:#d7262b;
  --navy:#23346e;
  --navy-dark:#1c2a5c;
  --ink:#141414;
  --text:#555;
  --white:#fff;
  --soft:#fdf5f4;
  --black:#000;
}
*{margin:0;padding:0;box-sizing:border-box}
html,body{width:1200px;height:4454px;overflow:hidden}
body{position:relative;font-family:'Montserrat',sans-serif;color:var(--ink);background:var(--white)}
.abs{position:absolute}
.display{font-family:'Michroma',sans-serif;font-weight:400;text-transform:uppercase;letter-spacing:1px}
.btn{position:absolute;background:var(--red);color:var(--white);font-family:'Oswald',sans-serif;font-weight:500;font-size:15px;display:flex;align-items:center;justify-content:center;gap:10px;text-decoration:none}
.photo{position:absolute}
/* header */
.header{position:absolute;left:0;top:0;width:1200px;height:130px;background:var(--soft)}
.topbar{position:absolute;left:400px;top:0;width:800px;height:45px;background:var(--red);color:var(--white);font-size:13px;display:flex;align-items:center;padding-left:88px;gap:0}
.topbar .item{display:flex;align-items:center;gap:10px;margin-right:56px}
.topbar .help{font-weight:600;margin-right:48px}
.topbar .ring{width:30px;height:30px;border:1.5px solid var(--white);border-radius:50%;display:flex;align-items:center;justify-content:center}
.brand{position:absolute;left:112px;top:34px;display:flex;align-items:center;gap:10px}
.brand .mark{width:22px;height:22px;background:var(--red);border-radius:50%}
.brand .name{font-family:'Montserrat',sans-serif;font-weight:600;font-size:17px;color:var(--navy);line-height:1.25;width:240px}
.nav{position:absolute;top:82px;left:435px;display:flex;gap:0;font-size:14px;color:#333}
.nav span{margin-right:36px}
/* hero */
.hero{position:absolute;left:0;top:130px;width:1200px;height:570px}
.hero .photo{inset:0;background:linear-gradient(135deg,#d9d6d0 0%,#c9c2b6 45%,#b8a54a 75%,#8a8a70 100%)}
.hero .shade{position:absolute;inset:0;background:rgba(0,0,0,.25)}
.hero h1{position:absolute;top:158px;width:1200px;text-align:center;color:var(--white);font-size:32px;line-height:44px}
.hero .tag{position:absolute;top:258px;width:1200px;text-align:center;color:var(--white);font-family:'Oswald',sans-serif;font-size:23px;letter-spacing:.5px}
/* about */
.about-box{left:122px;top:800px;width:315px;height:338px;background:var(--navy);border-radius:6px}
.framed{border:3px solid var(--red);border-radius:10px}
.about-photo{left:173px;top:840px;width:395px;height:343px;background:linear-gradient(160deg,#eeeeec,#d8d8d4 60%,#c47a3a)}
.h2{font-size:38px;color:var(--ink)}
.body-copy{font-size:14px;line-height:29px;color:var(--text)}
/* products */
.products{position:absolute;left:0;top:1290px;width:1200px;height:782px;background:var(--navy)}
.products .glow{position:absolute;inset:0;background:radial-gradient(circle at 35% 30%,rgba(255,255,255,.07),transparent 45%)}
.card{position:absolute;top:1435px;width:252px;height:455px;background:var(--white);border-radius:6px;padding:5px}
.card .thumb{width:242px;height:200px;border:1px solid #333;border-radius:4px}
.card h3{font-family:'Oswald',sans-serif;font-weight:500;font-size:21px;line-height:30px;margin:20px 10px 0 13px;color:var(--ink)}
.card p{font-size:14px;line-height:31px;color:var(--text);margin:10px 10px 0 13px}
.card .more{font-family:'Oswald',sans-serif;font-size:15px;color:var(--red);margin:8px 0 0 13px;display:block}
.dash{position:absolute;top:1949px;height:5px;width:42px;background:#8d97b8;border-radius:2px}
/* services */
.svc-icon{position:absolute;left:108px;width:137px;height:137px;border-radius:50%;background:var(--red);display:flex;align-items:center;justify-content:center}
.svc h3{font-size:17px;font-weight:500;line-height:32px;color:var(--ink)}
.svc p{font-size:15px;line-height:29px;color:#777}
.svc .more{font-family:'Oswald',sans-serif;color:var(--red);font-size:15px}
/* schedule */
.schedule{position:absolute;left:0;top:2830px;width:1200px;height:470px;background:var(--navy)}
/* testimonials */
.tcard{position:absolute;top:3480px;width:312px;height:360px;background:var(--white);box-shadow:0 2px 12px rgba(0,0,0,.14);text-align:center}
.avatar{width:110px;height:110px;border-radius:50%;margin:20px auto 0;background:linear-gradient(180deg,#d9d9d9,#9aa6b4)}
.tcard .who{font-size:16px;font-weight:500;margin-top:10px}
.tcard .role{font-size:14px;color:#444;margin-top:4px}
.tcard .q{position:absolute;left:12px;top:178px;font-size:34px;font-family:Georgia,serif;line-height:1}
.tcard p{font-size:14px;line-height:26px;color:#888;padding:0 22px;margin-top:18px}
.stars{color:#f4b400;font-size:19px;letter-spacing:1px;margin-top:8px}
/* footer */
.footer{position:absolute;left:0;top:3960px;width:1200px;height:494px;background:var(--black);color:var(--white)}
.footer h4{font-size:21px;font-weight:500}
.footer li{list-style:none;font-size:14px;line-height:28px}
.subscribe{position:absolute;left:888px;top:4110px;width:198px;height:235px;background:var(--navy);border-radius:6px;text-align:center;padding-top:30px}
</style>
</head>
<body>

<!-- Header -->
<header class="header">
  <div class="topbar">
    <span class="help">Need Help?</span>
    <span class="item"><span class="ring"><svg width="14" height="14" viewBox="0 0 24 24"><path fill="#fff" d="M6.6 10.8a15 15 0 006.6 6.6l2.2-2.2c.3-.3.7-.4 1-.2 1.1.4 2.3.6 3.6.6.6 0 1 .4 1 1V20c0 .6-.4 1-1 1A17 17 0 013 4c0-.6.4-1 1-1h3.5c.6 0 1 .4 1 1 0 1.3.2 2.5.6 3.6.1.3 0 .7-.2 1z"/></svg></span>+1 555 010 2040</span>
    <span class="item"><span class="ring"><svg width="14" height="14" viewBox="0 0 24 24"><path fill="#fff" d="M3 5h18v14H3z"/><path fill="none" stroke="#d7262b" stroke-width="2" d="M3 6l9 7 9-7"/></svg></span>info@coastalbreezecooling.example</span>
  </div>
  <div class="brand"><span class="mark"></span><span class="name">Coastal Breeze Cooling Company</span></div>
  <nav class="nav"><span>HOME</span><span>OUR PRODUCTS</span><span>OUR SERVICES</span><span>OUR BLOGS</span><span>ABOUT</span><span>CONTACT</span></nav>
</header>

<!-- Hero -->
<section class="hero">
  <div class="photo" role="img" aria-label="Couple relaxing on a yellow sofa in a cool living room under a wall air conditioner"></div>
  <div class="shade"></div>
  <h1 class="display">The Coastal Breeze<br>Cooling Company</h1>
  <div class="tag">SERVICE BEYOND COMPARISON</div>
  <a class="btn" style="left:513px;top:314px;width:170px;height:46px;background:var(--navy)">Get Started</a>
  <svg class="abs" style="left:0;top:505px" width="1200" height="70" viewBox="0 0 1200 70">
    <path d="M0 70 L0 52 Q300 40 600 10 Q900 40 1200 52 L1200 70 Z" fill="#fff"/>
    <path d="M0 50 Q300 36 600 4 Q900 36 1200 50 L1200 58 Q900 48 600 24 Q300 48 0 62 Z" fill="var(--red)"/>
  </svg>
</section>

<!-- About -->
<div class="abs about-box"></div>
<div class="photo framed about-photo" role="img" aria-label="Two technicians installing a wall-mounted air conditioner"></div>
<h2 class="abs display h2" style="left:622px;top:810px">About Us</h2>
<p class="abs body-copy" style="left:622px;top:877px;width:430px">Lorem Ipsum is simply dummy text of the printing and typesetting industry. Lorem Ipsum has been the industry's standard dummy text ever since the 1500s, when an unknown printer took a galley of type and scrambled it to make a type specimen book. It has survived not only five centuries, but also the leap into electronic typesetting, remaining essentially unchanged.</p>
<a class="btn" style="left:618px;top:1108px;width:171px;height:44px">Read More</a>

<!-- Products -->
<section class="products"><div class="glow"></div></section>
<svg class="abs" style="left:0;top:1280px" width="1200" height="60" viewBox="0 0 1200 60">
  <path d="M0 0 L1200 0 L1200 12 Q900 22 600 50 Q300 22 0 12 Z" fill="#fff"/>
  <path d="M0 10 Q300 20 600 48 Q900 20 1200 10 L1200 20 Q900 30 600 58 Q300 30 0 20 Z" fill="var(--red)"/>
</svg>
<h2 class="abs display" style="left:110px;top:1435px;color:#fff;font-size:33px;line-height:52px">Our<br>Products</h2>
<p class="abs" style="left:111px;top:1555px;width:260px;color:#fff;font-size:20px;line-height:38px">Lorem Ipsum is simply dummy text of the printing and typesetting industry. Lorem Ipsum has been the industry's</p>
<a class="btn" style="left:111px;top:1818px;width:171px;height:46px">Read More</a>

<div class="card" style="left:400px"><div class="thumb" role="img" aria-label="White split air conditioning unit" style="background:linear-gradient(180deg,#fafafa,#e2e2e2)"></div><h3>Air Conditioning Equipment</h3><p>Lorem Ipsum is simply dummy text of the printing and typesetting industry.</p><span class="more">Read More</span></div>
<div class="card" style="left:672px"><div class="thumb" role="img" aria-label="Copper pipes and capacitor parts" style="background:linear-gradient(135deg,#f3e3d8,#d9875c 55%,#b5b5b5)"></div><h3>Air Conditioning Parts</h3><p>Lorem Ipsum is simply dummy text of the printing and typesetting industry. Lorem Ipsum has been the</p><span class="more">Read More</span></div>
<div class="card" style="left:943px"><div class="thumb" role="img" aria-label="Hand holding an air conditioning filter" style="background:linear-gradient(135deg,#f2f2f2,#cfd3d6)"></div><h3>Air Conditioning Filters</h3><p>Lorem Ipsum is simply dummy text of the printing and typesetting industry. Lorem Ipsum has been the</p><span class="more">Read More</span></div>
<span class="dash" style="left:520px;background:#fff"></span>
<span class="dash" style="left:576px"></span>
<span class="dash" style="left:632px"></span>

<!-- Services -->
<h2 class="abs display h2" style="left:108px;top:2195px">Our Services</h2>
<div class="svc-icon" style="top:2280px"><svg width="70" height="70" viewBox="0 0 70 70" fill="none" stroke="#fff" stroke-width="2.5"><path d="M8 32 L32 12 L56 32"/><path d="M14 28 V60 H50 V28"/><rect x="27" y="42" width="11" height="18"/><circle cx="60" cy="40" r="7"/><path d="M60 47 V60"/></svg></div>
<div class="abs svc" style="left:260px;top:2285px;width:330px"><h3>Residential properties Maintenance And Installing Hvac Systems</h3><p style="margin-top:4px">Lorem Ipsum is simply dummy text of the printing and typesetting industry.</p><span class="more">Read More</span></div>
<div class="svc-icon" style="top:2453px"><svg width="70" height="70" viewBox="0 0 70 70" fill="none" stroke="#fff" stroke-width="2.5"><rect x="24" y="8" width="26" height="54"/><rect x="8" y="30" width="16" height="32"/><path d="M30 16h4M40 16h4M30 26h4M40 26h4M30 36h4M40 36h4M30 46h4M40 46h4M13 38v4M18 38v4M13 48v4M18 48v4"/></svg></div>
<div class="abs svc" style="left:260px;top:2458px;width:340px"><h3>Commercial Properties Maintenance And Installing Hvac Systems</h3><p style="margin-top:4px">Lorem Ipsum is simply dummy text of the printing and typesetting industry.</p><span class="more">Read More</span></div>
<a class="btn" style="left:111px;top:2666px;width:171px;height:47px">Read More</a>
<div class="abs" style="left:615px;top:2235px;width:315px;height:285px;background:var(--navy);border-radius:6px"></div>
<div class="photo framed" style="left:673px;top:2296px;width:395px;height:344px;background:linear-gradient(150deg,#f1eeec,#d8d4d0 55%,#2e3a66)" role="img" aria-label="Technician cleaning an indoor air conditioning unit"></div>

<!-- Schedule -->
<section class="schedule" role="img" aria-label="Faint air conditioning grille image on navy background" style="background:linear-gradient(120deg,var(--navy-dark),var(--navy) 50%,#2a3d7a)"></section>
<h2 class="abs display" style="left:0;top:2945px;width:1200px;text-align:center;color:#fff;font-size:37px">Schedule An Appointment</h2>
<p class="abs" style="left:220px;top:3028px;width:760px;text-align:center;color:#fff;font-size:14px;line-height:29px">Lorem Ipsum is simply dummy text of the printing and typesetting industry. Lorem Ipsum has been the industry's standard dummy text ever since the 1500s,</p>
<a class="btn" style="left:514px;top:3115px;width:170px;height:45px"><svg width="16" height="16" viewBox="0 0 24 24"><path fill="#fff" d="M6.6 10.8a15 15 0 006.6 6.6l2.2-2.2c.3-.3.7-.4 1-.2 1.1.4 2.3.6 3.6.6.6 0 1 .4 1 1V20c0 .6-.4 1-1 1A17 17 0 013 4c0-.6.4-1 1-1h3.5c.6 0 1 .4 1 1 0 1.3.2 2.5.6 3.6.1.3 0 .7-.2 1z"/></svg>+1 555 010 2040</a>
<svg class="abs" style="left:0;top:3240px" width="1200" height="62" viewBox="0 0 1200 62">
  <path d="M0 62 L0 52 Q300 40 600 8 Q900 40 1200 52 L1200 62 Z" fill="#fff"/>
  <path d="M0 48 Q300 34 600 2 Q900 34 1200 48 L1200 56 Q900 46 600 22 Q300 46 0 60 Z" fill="var(--red)"/>
</svg>

<!-- Testimonials -->
<h2 class="abs display h2" style="left:0;top:3378px;width:1200px;text-align:center">Our Testimonials</h2>
<div class="tcard" style="left:110px"><div class="avatar" role="img" aria-label="Client portrait"></div><div class="who">Marcus</div><div class="role">Client</div><span class="q">&ldquo;</span><p>Lorem Ipsum is simply dummy text of the printing and typesetting industry. Lorem Ipsum has been the industry's standard dummy text ever since the</p><div class="stars">★★★★★</div></div>
<div class="tcard" style="left:443px"><div class="avatar" role="img" aria-label="Client portrait"></div><div class="who">Dana</div><div class="role">Client</div><span class="q">&ldquo;</span><p>Lorem Ipsum is simply dummy text of the printing and typesetting industry. Lorem Ipsum has been the industry's standard dummy text ever since the</p><div class="stars">★★★★★</div></div>
<div class="tcard" style="left:774px"><div class="avatar" role="img" aria-label="Client portrait"></div><div class="who">Elena</div><div class="role">Client</div><span class="q">&ldquo;</span><p>Lorem Ipsum is simply dummy text of the printing and typesetting industry. Lorem Ipsum has been the industry's standard dummy text ever since the</p><div class="stars">★★★★★</div></div>
<svg class="abs" style="left:540px;top:3876px" width="110" height="28" viewBox="0 0 110 28">
  <circle cx="18" cy="14" r="12" fill="none" stroke="var(--red)" stroke-width="2"/><circle cx="18" cy="14" r="7" fill="var(--red)"/>
  <circle cx="48" cy="14" r="6" fill="var(--red)"/><circle cx="72" cy="14" r="6" fill="var(--red)"/><circle cx="97" cy="14" r="6" fill="var(--red)"/>
</svg>

<!-- Footer -->
<footer class="footer">
  <svg class="abs" style="left:0;top:0" width="1200" height="60" viewBox="0 0 1200 60">
    <path d="M0 0 L1200 0 L1200 12 Q900 22 600 50 Q300 22 0 12 Z" fill="#fff"/>
    <path d="M0 10 Q300 20 600 48 Q900 20 1200 10 L1200 20 Q900 30 600 58 Q300 30 0 20 Z" fill="var(--red)"/>
  </svg>
  <div class="abs" style="left:110px;top:178px;display:flex;align-items:center;gap:10px"><span style="width:20px;height:20px;background:var(--red);border-radius:50%"></span><span style="font-weight:600;font-size:17px;line-height:1.25;width:200px">Coastal Breeze Cooling Company</span></div>
  <div class="abs" style="left:407px;top:150px"><h4>Page Links</h4><ul style="margin-top:18px;margin-left:3px"><li>Home</li><li>Our Products</li><li>Our Services</li><li>Our Blogs</li><li>About</li><li>Contact</li></ul></div>
  <div class="abs" style="left:632px;top:150px"><h4>Contact Details</h4><ul style="margin-top:18px;font-size:14px">
    <li><span style="color:var(--red)">&#9990;</span> +1 555 010 2040</li>
    <li><span style="color:var(--red)">&#9993;</span> hello@coastalbreeze.example</li>
    <li><svg width="12" height="14" viewBox="0 0 12 16"><path fill="var(--red)" d="M6 0a6 6 0 016 6c0 4-6 10-6 10S0 10 0 6a6 6 0 016-6z"/><circle cx="6" cy="6" r="2" fill="#000"/></svg> Lorem Ipsum Lorem</li>
    <li style="padding-left:18px">lorem Ipsum Lorem</li></ul></div>
  <div class="subscribe" style="top:150px">
    <h4>Subscribe</h4>
    <p style="font-size:13px;line-height:28px;margin:8px 16px 0">Are you interested in following us for Getting Business Update</p>
    <div style="margin:14px auto 0;width:166px;height:38px;border:1.5px solid #fff;border-radius:20px;display:flex;align-items:center;justify-content:space-between;padding:0 4px 0 12px;font-size:10px">Your Email Address<span style="width:28px;height:28px;border:1.5px solid #fff;border-radius:50%;display:flex;align-items:center;justify-content:center">&#8594;</span></div>
  </div>
  <div class="abs" style="left:108px;top:450px;width:976px;height:1px;background:#fff"></div>
  <p class="abs" style="left:0;top:464px;width:1200px;text-align:center;font-size:13px">© 2024 The Coastal Breeze Cooling Company I All Rights</p>
</footer>

</body>
</html>
```